VOMRA Pty Ltd Business Card

Looking for a simple yet eye-catching double-sided business card design using my company logo on one side and contact details on the other.

Target Market(s)

Government

Industry/Entity Type

Communication Systems Engineering

Contact Information for Business Card

VOMRA Pty Ltd

Requirements
Nice to have
• Would be great to have a QR code so details can be scanned into contacts

```html
<!DOCTYPE html>
<html lang="en">
<head>
<meta charset="utf-8">
<title>VOMRA Pty Ltd Business Card</title>
<link rel="stylesheet" href="https://fonts.googleapis.com/css2?family=Open+Sans:wght@400;600;700&display=swap">
<style>
  :root {
    --page: #e9e6e2;
    --slate: #37414a;
    --slate-deep: #2a323a;
    --ink: #323c45;
    --paper: #ffffff;
    --swoosh-light: #f1f1f1;
    --swoosh-mid: #d9d9d9;
  }
  * { margin: 0; padding: 0; box-sizing: border-box; }
  html, body { width: 1200px; height: 780px; overflow: hidden; }
  body {
    background: var(--page);
    font-family: "Open Sans", sans-serif;
    color: var(--ink);
    position: relative;
  }
  .card {
    position: absolute;
    top: 105px;
    width: 330px;
    height: 570px;
    border-radius: 22px;
    overflow: hidden;
    box-shadow: 0 6px 18px rgba(0,0,0,0.18);
  }
  /* Back side */
  .card-back { left: 215px; background: var(--slate); }
  .back-brand {
    position: absolute;
    left: 165px;
    top: 215px;
    transform: translate(-50%, -50%) rotate(90deg);
    font-weight: 700;
    font-size: 84px;
    letter-spacing: 10px;
    color: var(--slate-deep);
    white-space: nowrap;
  }
  .back-dot {
    position: absolute;
    left: 115px;
    top: 410px;
    width: 100px;
    height: 100px;
    border-radius: 50%;
    background: var(--slate-deep);
  }
  /* Front side */
  .card-front { left: 655px; background: var(--paper); border: 1px solid #dcdcdc; }
  .front-brand {
    position: absolute;
    left: 40px;
    top: 60px;
    display: flex;
    align-items: center;
    gap: 16px;
  }
  .front-brand .brand-dot {
    width: 52px; height: 52px; border-radius: 50%;
    background: var(--ink);
  }
  .front-brand .brand-name {
    font-weight: 700;
    font-size: 46px;
    letter-spacing: 5px;
    color: var(--ink);
  }
  .swoosh { position: absolute; left: 0; bottom: 0; width: 330px; height: 330px; }
  .person {
    position: absolute;
    left: 0; right: 0;
    top: 222px;
    text-align: center;
  }
  .person-name { font-weight: 700; font-size: 27px; line-height: 1.1; }
  .person-role { font-weight: 600; font-size: 15px; margin-top: 2px; }
  .contact-icons {
    display: flex; justify-content: center; gap: 8px; margin: 14px 0 10px;
  }
  .contact-icons svg { width: 26px; height: 26px; }
  .contact-lines { font-size: 16px; line-height: 1.3; }
  .address {
    position: absolute;
    left: 0; right: 0;
    bottom: 40px;
    text-align: center;
    font-size: 16px;
    line-height: 1.3;
  }
  .address svg { width: 26px; height: 26px; display: block; margin: 0 auto 8px; }
</style>
</head>
<body>

  <section class="card card-back" aria-label="Card back">
    <div class="back-brand">VOMRA</div>
    <div class="back-dot"></div>
  </section>

  <section class="card card-front" aria-label="Card front">
    <div class="front-brand">
      <span class="brand-dot"></span>
      <span class="brand-name">VOMRA</span>
    </div>

    <svg class="swoosh" viewBox="0 0 330 330" preserveAspectRatio="none" aria-hidden="true">
      <path d="M0 330 L0 120 C60 150 130 140 200 100 C260 65 300 30 330 0 L330 330 Z" fill="var(--swoosh-mid)"/>
      <path d="M0 330 L0 140 C90 160 190 150 260 110 C295 90 318 70 330 55 L330 330 Z" fill="var(--swoosh-light)"/>
      <path d="M0 330 L0 175 C70 170 150 160 210 140 C260 125 300 110 330 95 L330 330 Z" fill="var(--swoosh-mid)" opacity="0.55"/>
      <path d="M0 330 L0 190 C80 180 160 168 230 150 C280 138 310 125 330 115 L330 330 Z" fill="var(--paper)"/>
    </svg>

    <div class="person">
      <div class="person-name">Jordan Whitfield</div>
      <div class="person-role">Co-Founder</div>
      <div class="contact-icons">
        <svg viewBox="0 0 26 26" aria-label="Phone"><circle cx="13" cy="13" r="13" fill="var(--ink)"/><path d="M9 7.5c.6-.4 1.2 0 1.5.6l1 2c.2.5 0 1-.4 1.3l-.6.5c.6 1.3 1.6 2.3 2.9 2.9l.5-.6c.3-.4.8-.6 1.3-.4l2 1c.6.3 1 .9.6 1.5-.6 1-1.6 1.6-2.7 1.3-3.4-1-6-3.6-7-7-.3-1.1.3-2.1 1.3-2.7z" fill="#fff"/></svg>
        <svg viewBox="0 0 26 26" aria-label="Email"><circle cx="13" cy="13" r="13" fill="var(--ink)"/><rect x="7" y="9" width="12" height="9" rx="1" fill="none" stroke="#fff" stroke-width="1.4"/><path d="M7.5 9.5l5.5 4.5 5.5-4.5" fill="none" stroke="#fff" stroke-width="1.4"/></svg>
        <svg viewBox="0 0 26 26" aria-label="Website"><circle cx="13" cy="13" r="13" fill="var(--ink)"/><circle cx="13" cy="13" r="6.5" fill="none" stroke="#fff" stroke-width="1.4"/><ellipse cx="13" cy="13" rx="2.8" ry="6.5" fill="none" stroke="#fff" stroke-width="1.2"/><path d="M6.5 13h13" stroke="#fff" stroke-width="1.2"/></svg>
      </div>
      <div class="contact-lines">
        <div>(555) 014-2390</div>
        <div>www.vomra.com.au</div>
        <div>admin@vomra.com.au</div>
      </div>
    </div>

    <div class="address">
      <svg viewBox="0 0 26 26" aria-label="Location"><circle cx="13" cy="13" r="13" fill="var(--ink)"/><path d="M13 6.5a4.5 4.5 0 0 0-4.5 4.5c0 3.3 4.5 8.5 4.5 8.5s4.5-5.2 4.5-8.5A4.5 4.5 0 0 0 13 6.5z" fill="#fff"/><circle cx="13" cy="11" r="1.7" fill="var(--ink)"/></svg>
      <div>27-29 Marlow Street Eastwood</div>
      <div>NSW 2122 Australia</div>
    </div>
  </section>

</body>
</html>
```